Liron Vasek Website

Website for my son who is in 7th grade in the US. This will prepare him to show people his accomplishments when applying for a job or going to college. It should have:
* A picture (or multiple pictures)
* A resume page
* A place to share your accomplishments
* Links to his other social profiles
* A contact form

Great to include:
* Internships (show some photos of it along with what you’ve learned).
* Volunteer work.
* A side hustle that you want to highlight

Website sample I like:
https://belinamorud.sitefolio-demo.com/belinamorudtavik

Target Market(s)

For jobs and colleges admissions.

Number of Pages Required

5+ page

Colors

Designer to choose colors to be used in the design.

Requirements
Must have
• * A picture (or multiple pictures)
• * A resume page
• * A place to share your accomplishments
• * Links to his other social profiles
• * A contact form
Nice to have
• Great to include:
• * Internships (show some photos of it along with what you’ve learned).
• * Volunteer work.
• * A side hustle that you want to highlight

```html
<!DOCTYPE html>
<html lang="en">
<head>
<meta charset="utf-8">
<title>Liron Vasek</title>
<link rel="stylesheet" href="https://fonts.googleapis.com/css2?family=Lato:wght@400;700;900&display=swap">
<style>
:root{
  --ink:#2e2e2e;
  --text:#444;
  --nav-bg:#f4f4f4;
  --hero-bg:#f7f7f7;
  --blue:#2196e0;
  --nav-active:#2a9fd8;
  --gold:#f0b20f;
  --green:#3dba85;
  --footer:#2d2d2d;
  --line:#cfcfcf;
}
*{box-sizing:border-box;margin:0;padding:0}
html,body{width:1200px;height:3161px;overflow:hidden}
body{position:relative;background:#fff;font-family:'Lato',sans-serif;color:var(--text)}
.abs{position:absolute}
.nav{display:flex;justify-content:center;gap:39px;font-weight:700;font-size:14px;letter-spacing:.2px;text-transform:uppercase}
.nav a{color:var(--ink);text-decoration:none}
.topbar{left:0;top:0;width:1200px;height:54px;background:var(--nav-bg);padding-top:19px}
.topbar .active{color:var(--nav-active)}
.hero{left:0;top:54px;width:1200px;height:660px;background:var(--hero-bg)}
.site-title{left:0;top:68px;width:1200px;text-align:center;font-weight:900;font-size:56px;color:var(--ink);line-height:1}
.hero-frame{left:75px;top:147px;width:1051px;height:559px;border:4px solid #e0e0e0;background:#fff}
.photo{display:block}
.hero-photo{width:100%;height:100%;background:linear-gradient(100deg,#f1f3f2 0%,#e6e2d6 30%,#b9b2a4 55%,#8d8f95 80%,#c5c7cb 100%)}
.section-title{font-weight:700;font-size:29px;color:var(--ink);text-transform:uppercase;line-height:1}
.center{text-align:center}
.body-copy{font-size:14.5px;line-height:27.6px}
.btn{display:flex;align-items:center;justify-content:center;background:var(--blue);color:#fff;font-weight:700;font-size:14px;text-transform:uppercase;text-decoration:none}
.band{left:0;width:1200px;height:355px}
.band .band-photo{position:absolute;left:0;top:0;width:587px;height:355px}
.band .band-title{position:absolute;left:613px;color:#fff;font-weight:700;font-size:30px;text-transform:uppercase;line-height:1}
.band .body-copy{position:absolute;left:613px;width:505px;color:#fff;font-size:14px}
.field{border:1px solid var(--line);background:#fff;font-size:14px;color:var(--ink);padding:0 14px;display:flex;align-items:center}
.footer{left:0;top:2974px;width:1200px;height:187px;background:var(--footer)}
.footer .nav a{color:#fff}
.copyright{left:0;top:3057px;width:1200px;text-align:center;font-size:12.5px;color:#bbb}
.social{left:0;top:3090px;width:1200px;display:flex;justify-content:center;gap:22px}
.social span{width:20px;height:20px;border-radius:50%;background:#bdbdbd;display:block}
</style>
</head>
<body>

<header class="abs topbar">
  <nav class="nav">
    <a class="active" href="#">Home</a><a href="#">Portfolio</a><a href="#">Resume</a><a href="#">Achievements</a><a href="#">Blog</a><a href="#">Contact</a>
  </nav>
</header>

<section class="abs hero"></section>
<h1 class="abs site-title">LIRON VASEK</h1>
<div class="abs hero-frame">
  <div class="photo hero-photo" role="img" aria-label="Smiling boy working on a laptop by a bright window"></div>
</div>

<h2 class="abs section-title center" style="left:0;top:756px;width:1200px">About Liron Vasek</h2>
<p class="abs body-copy center" style="left:170px;top:805px;width:860px">Lorem ipsum dolor sit amet, consectetur adipiscing elit. Duis ornare purus ut ligula blandit euismod. Ut tincidunt vehicula tristique. Sed non pharetra magna. Aenean molestie augue feugiat molestie maximus. Donec fringilla ligula eros, et vestibulum turpis dapibus ac. Mauris et tempus neque, et accumsan nunc. Proin elementum finibus turpis at porta. Fusce nulla nibh, vehicula id mollis ac, rhoncus sit amet leo.</p>
<a class="abs btn" href="#" style="left:524px;top:956px;width:152px;height:44px">Read More</a>

<div class="abs photo" style="left:75px;top:1047px;width:340px;height:234px;background:linear-gradient(135deg,#eceae6,#d9d5cc 50%,#6f8f5c)" role="img" aria-label="Boy using a tablet beside a small model house and wind turbine"></div>
<div class="abs photo" style="left:431px;top:1047px;width:340px;height:234px;background:linear-gradient(135deg,#f3f3f1,#e2ddd4 50%,#b97a3e)" role="img" aria-label="Boy reading a tablet on a sofa"></div>
<div class="abs photo" style="left:787px;top:1047px;width:340px;height:234px;background:linear-gradient(135deg,#8a7a6c,#c79a7e 45%,#c0302a)" role="img" aria-label="Close-up of a smiling boy in a red shirt"></div>

<section class="abs band" style="top:1339px;background:var(--gold)">
  <div class="band-photo" style="background:radial-gradient(circle at 45% 45%,#8e8490,#5a5058 60%,#3e373d)" role="img" aria-label="Boy holding a trophy and medals"></div>
  <h2 class="band-title" style="top:63px">Accomplishments</h2>
  <p class="body-copy" style="top:111px">Lorem ipsum dolor sit amet, consectetur adipiscing elit. Duis ornare purus ut ligula blandit euismod. Ut tincidunt vehicula tristique. Sed non pharetra magna. Aenean molestie augue feugiat molestie maximus. Donec fringilla ligula eros, et vestibulum turpis dapibus ac.</p>
  <a class="btn" href="#" style="position:absolute;left:613px;top:245px;width:173px;height:43px">View Achivements</a>
</section>

<h2 class="abs section-title" style="left:74px;top:1776px;font-size:28px">Internships</h2>
<p class="abs body-copy" style="left:75px;top:1825px;width:505px;font-size:14px">Lorem ipsum dolor sit amet, consectetur adipiscing elit. Duis ornare purus ut ligula blandit euismod. Ut tincidunt vehicula tristique. Sed non pharetra magna. Aenean molestie augue feugiat molestie maximus. Donec fringilla ligula eros, et vestibulum turpis dapibus ac. Mauris et tempus neque, et accumsan nunc. Proin elementum finibus turpis at porta. Fusce nulla nibh, vehicula id mollis ac, rhoncus sit amet leo.</p>
<a class="abs btn" href="#" style="left:75px;top:2021px;width:153px;height:44px">Read More</a>

<div class="abs photo" style="left:613px;top:1747px;width:250px;height:165px;background:linear-gradient(135deg,#dfe6ea,#b9c4c9 55%,#555)" role="img" aria-label="Boy building a small robot"></div>
<div class="abs photo" style="left:877px;top:1747px;width:250px;height:165px;background:linear-gradient(135deg,#7b6a5c,#3f6fb3 50%,#cfcac2)" role="img" aria-label="Boy on a video call with a laptop"></div>
<div class="abs photo" style="left:613px;top:1929px;width:250px;height:164px;background:linear-gradient(135deg,#f2f2f2,#d6d6d6 50%,#c8782f)" role="img" aria-label="Boy working at a desktop computer"></div>
<div class="abs photo" style="left:877px;top:1929px;width:250px;height:164px;background:linear-gradient(135deg,#e2e2e0,#9fb5cf 50%,#c9b8a2)" role="img" aria-label="Boy and a mentor looking at a laptop"></div>

<section class="abs band" style="top:2156px;background:var(--green)">
  <div class="band-photo" style="background:linear-gradient(135deg,#2f4b22,#6f9a3b 45%,#b47a3a 75%,#2d3a1e)" role="img" aria-label="Boy holding a crate of plastic bottles for recycling in a park"></div>
  <h2 class="band-title" style="top:63px">Volunteer Work</h2>
  <p class="body-copy" style="top:111px">Lorem ipsum dolor sit amet, consectetur adipiscing elit. Duis ornare purus ut ligula blandit euismod. Ut tincidunt vehicula tristique. Sed non pharetra magna. Aenean molestie augue feugiat molestie maximus. Donec fringilla ligula eros, et vestibulum turpis dapibus ac.</p>
  <a class="btn" href="#" style="position:absolute;left:613px;top:245px;width:173px;height:43px">Read More</a>
</section>

<h2 class="abs section-title center" style="left:0;top:2561px;width:1200px">Contact Us</h2>
<div class="abs field" style="left:254px;top:2623px;width:333px;height:45px">Name</div>
<div class="abs field" style="left:612px;top:2623px;width:334px;height:45px">Email Address</div>
<div class="abs field" style="left:254px;top:2685px;width:333px;height:44px">Phone No</div>
<div class="abs field" style="left:612px;top:2685px;width:334px;height:44px">Subject</div>
<div class="abs field" style="left:254px;top:2745px;width:692px;height:112px;align-items:flex-start;padding-top:12px">Message</div>
<a class="abs btn" href="#" style="left:524px;top:2876px;width:152px;height:44px">Submit</a>

<footer class="abs footer">
  <nav class="nav" style="margin-top:47px">
    <a href="#">Home</a><a href="#">Portfolio</a><a href="#">Resume</a><a href="#">Achievements</a><a href="#">Blog</a><a href="#">Contact</a>
  </nav>
</footer>
<p class="abs copyright">Copyright © 2019, Company Name  All Right reserved</p>
<div class="abs social" aria-label="Social profiles"><span></span><span></span><span></span><span></span><span></span></div>

</body>
</html>
```